Business card por a urban DJ, up scale audience target

Need a sober design, modern, conservative colors but i can consider some options, y play rnb, hip hop, EDM and top40.

Business card for contact and personal info, double sided, use logo attrached please; im 42 so i need a card acording to my age an target audience.

Target Market(s)

Adult people, up scale audience

Industry/Entity Type

Music Download

Contact Information for Business Card

Cel (318) 4207265518 www.lumadrift.com

Requirements
Must have
• open mind
Nice to have
• open mind
Should not have
• DJ

```html
<!DOCTYPE html>
<html lang="en">
<head>
<meta charset="utf-8">
<title>Lumadrift Business Card</title>
<link href="https://fonts.googleapis.com/css2?family=Open+Sans:wght@400;700;800&display=swap" rel="stylesheet">
<style>
  :root {
    --ink: #0b0b0b;
    --paper: #ffffff;
    --backdrop: #d9d9d9;
    --muted: #222222;
  }
  * { box-sizing: border-box; margin: 0; padding: 0; }
  html, body {
    width: 1200px; height: 900px; overflow: hidden;
    background: var(--backdrop);
    font-family: "Open Sans", Arial, sans-serif;
  }
  .canvas { position: relative; width: 1200px; height: 900px; }
  .card {
    position: absolute; width: 600px; height: 343px;
    overflow: hidden;
    box-shadow: 0 6px 18px rgba(0,0,0,.18);
  }

  /* Front */
  .card-front {
    left: 100px; top: 80px;
    background: var(--ink); color: var(--paper);
    display: flex; flex-direction: column; align-items: center; justify-content: center;
  }
  .brand {
    display: flex; align-items: center; gap: 14px;
  }
  .brand-mark { width: 22px; height: 22px; background: currentColor; }
  .brand-name {
    font-weight: 800; font-size: 96px; line-height: 1; letter-spacing: 2px;
  }
  .front-url {
    margin-top: 22px;
    font-size: 21px; letter-spacing: 6px; font-weight: 400;
  }

  /* Back */
  .card-back {
    left: 500px; top: 480px;
    background: var(--paper); color: var(--ink);
  }
  .top-rule {
    position: absolute; left: 0; right: 0; top: 30px;
    height: 1.5px; background: var(--ink);
  }
  .contact {
    position: absolute; left: 26px; top: 118px;
  }
  .contact-name { font-weight: 700; font-size: 22px; line-height: 1.1; }
  .contact-role { font-size: 13px; color: var(--muted); margin-top: 2px; }
  .contact-line {
    display: flex; align-items: center; gap: 7px;
    font-size: 13.5px; margin-top: 3px;
  }
  .contact-line svg { width: 11px; height: 11px; flex: none; }
  .back-brand {
    position: absolute; right: 26px; top: 100px;
    color: var(--ink);
  }
  .back-brand .brand-name { font-size: 64px; }
  .back-brand .brand-mark { width: 16px; height: 16px; }
  .level-band {
    position: absolute; left: 0; right: 0; bottom: 0; height: 150px;
    background: linear-gradient(to bottom, rgba(11,11,11,0) 0%, rgba(11,11,11,.35) 45%, var(--ink) 100%);
  }
</style>
</head>
<body>
<main class="canvas">
  <section class="card card-front" aria-label="Card front">
    <div class="brand">
      <span class="brand-mark"></span>
      <span class="brand-name">LUMA</span>
    </div>
    <p class="front-url">www.lumadrift.com</p>
  </section>

  <section class="card card-back" aria-label="Card back">
    <div class="top-rule"></div>
    <div class="contact">
      <h1 class="contact-name">Marco Vell</h1>
      <p class="contact-role">CEO</p>
      <p class="contact-line">
        <svg viewBox="0 0 10 12" aria-hidden="true"><rect x="1.5" y="0.5" width="7" height="11" rx="1.2" fill="none" stroke="currentColor" stroke-width="1.2"/><rect x="4" y="9" width="2" height="1" fill="currentColor"/></svg>
        (318) 4207265518
      </p>
      <p class="contact-line">
        <svg viewBox="0 0 12 12" aria-hidden="true"><circle cx="6" cy="6" r="5.2" fill="none" stroke="currentColor" stroke-width="1.1"/><ellipse cx="6" cy="6" rx="2.3" ry="5.2" fill="none" stroke="currentColor" stroke-width="1"/><line x1="0.8" y1="6" x2="11.2" y2="6" stroke="currentColor" stroke-width="1"/></svg>
        www.lumadrift.com
      </p>
    </div>
    <div class="brand back-brand">
      <span class="brand-mark"></span>
      <span class="brand-name">LUMA</span>
    </div>
    <div class="level-band" role="img" aria-label="Row of black audio level bars rising from left to right along the bottom edge"></div>
  </section>
</main>
</body>
</html>
```